Custom Seed Packet design for Flower Farm

We need a design for our seeds packets.
The design will be a kind of "fill in the blanks" as we need the design to be adaptable for multiple varieties of seed. We will be using the design for a rubber stamp.
Our seed packets are 90x90mm in size.
Black logo only. No colour required.
A vintage botanical influence is desired.
Will need to include the following info,
"Wrenfield Gable Co logo" , "Seeds", "Plant Type", "Variety", "Harvested"

```html
<!DOCTYPE html>
<html lang="en">
<head>
<meta charset="utf-8">
<title>Seed Packet Stamp – Wrenfield Gable Co Flower Farm</title>
<link href="https://fonts.googleapis.com/css2?family=Federo&family=Cabin:wght@400&display=swap" rel="stylesheet">
<style>
  :root {
    --kraft: #d9c7a3;
    --kraft-shade: #bfa97f;
    --ink: #1c1a17;
  }
  * { box-sizing: border-box; margin: 0; padding: 0; }
  html, body {
    width: 1122px; height: 1200px; overflow: hidden;
    background: var(--kraft);
  }
  .packet-label {
    position: absolute; left: 111px; top: 150px;
    width: 900px; height: 900px;
    border: 2px solid var(--ink);
    color: var(--ink);
  }
  .rule { position: absolute; left: 190px; width: 519px; height: 20px; }
  .rule--top { top: 41px; }
  .rule--bottom { top: 837px; }
  .rule-line { position: absolute; top: 9px; height: 2px; background: var(--ink); }
  .rule-line--left { left: 8px; width: 185px; }
  .rule-line--right { right: 8px; width: 185px; }
  .rule-end { position: absolute; top: 5px; width: 10px; height: 10px; background: var(--ink); transform: rotate(45deg); }
  .rule-end--left { left: 0; }
  .rule-end--right { right: 0; }
  .rule-flourish {
    position: absolute; left: 199px; top: 0; width: 121px; height: 20px;
    background: var(--kraft-shade); border-radius: 10px;
  }
  .botanical {
    position: absolute; background: var(--kraft-shade); border-radius: 40% 40% 30% 30%;
    opacity: .75;
  }
  .botanical--top-left { left: 4px; top: 80px; width: 194px; height: 219px; }
  .botanical--top-right { right: 4px; top: 80px; width: 194px; height: 219px; }
  .botanical--bottom-left { left: 4px; top: 582px; width: 153px; height: 312px; }
  .botanical--bottom-right { right: 4px; top: 582px; width: 153px; height: 312px; }
  .botanical--poppies { left: 271px; top: 505px; width: 216px; height: 159px; border-radius: 50%; }
  .packet-title {
    position: absolute; left: 0; right: 0; top: 118px;
    text-align: center;
    font-family: "Federo", sans-serif; font-size: 118px; line-height: 1;
    letter-spacing: 2px;
  }
  .fields { position: absolute; left: 103px; top: 290px; width: 717px; list-style: none; }
  .field {
    display: flex; align-items: flex-end; height: 48.5px;
    font-family: "Cabin", sans-serif; font-size: 21px;
  }
  .field-label { padding-right: 8px; }
  .field-line { flex: 1; border-bottom: 1.5px solid var(--ink); margin-bottom: 5px; }
  .brand-name {
    position: absolute; left: 200px; top: 712px; width: 500px;
    text-align: center;
    font-family: "Cabin", sans-serif; font-weight: 400; font-size: 30px;
    line-height: 1.35; letter-spacing: 1px; color: var(--ink);
  }
</style>
</head>
<body>
  <section class="packet-label">
    <div class="rule rule--top">
      <span class="rule-end rule-end--left"></span><span class="rule-line rule-line--left"></span>
      <span class="rule-flourish" role="img" aria-label="Small vintage scroll flourish"></span>
      <span class="rule-line rule-line--right"></span><span class="rule-end rule-end--right"></span>
    </div>

    <div class="botanical botanical--top-left" role="img" aria-label="Line drawing of blossoming flower sprig"></div>
    <div class="botanical botanical--top-right" role="img" aria-label="Line drawing of blossoming flower sprig"></div>

    <h1 class="packet-title">Seeds</h1>

    <ul class="fields">
      <li class="field"><span class="field-label">Seeds</span><span class="field-line"></span></li>
      <li class="field"><span class="field-label">Plant Type</span><span class="field-line"></span></li>
      <li class="field"><span class="field-label">Variety</span><span class="field-line"></span></li>
      <li class="field"><span class="field-label">Harvested</span><span class="field-line"></span></li>
    </ul>

    <div class="botanical botanical--poppies" role="img" aria-label="Line drawing of three poppy blooms"></div>
    <p class="brand-name">Wrenfield Gable Co<br>Flower Farm</p>

    <div class="botanical botanical--bottom-left" role="img" aria-label="Line drawing of leafy botanical stem"></div>
    <div class="botanical botanical--bottom-right" role="img" aria-label="Line drawing of leafy botanical stem"></div>

    <div class="rule rule--bottom">
      <span class="rule-end rule-end--left"></span><span class="rule-line rule-line--left"></span>
      <span class="rule-flourish" role="img" aria-label="Small vintage scroll flourish"></span>
      <span class="rule-line rule-line--right"></span><span class="rule-end rule-end--right"></span>
    </div>
  </section>
</body>
</html>
```